Business Card Design using new attached logo

We are a family run Plumbing and Heating firm looking to improve our company image with an improved business card and new logo.We are looking to keep the company colour (Blue) involved in our design

Reason: New logo added which needs to be incorporated on designs

Industry/Entity Type

Business

Contact Information for Business Card

See attachment of all info required.

Requirements
Must have
• We have just picked a new company logo which is attached.
• Could you please provide your business card designs using this logo.
• We are looking for the logo on the back as well as the front with all the info required

```html
<!DOCTYPE html>
<html lang="en">
<head>
<meta charset="utf-8">
<title>HLM Services – Business Cards</title>
<link rel="stylesheet" href="https://fonts.googleapis.com/css2?family=Arimo:wght@400;700&family=Tinos:wght@400;700&display=swap">
<style>
  :root {
    --backdrop: #e9e6e1;
    --card-white: #ffffff;
    --band-blue: #0a74f0;
    --panel-navy: #071468;
    --brand-blue: #3b5a9c;
    --text-light: #ffffff;
    --shadow: rgba(0, 0, 0, 0.28);
  }
  * { margin: 0; padding: 0; box-sizing: border-box; }
  html, body {
    width: 1200px;
    height: 1116px;
    overflow: hidden;
    background: var(--backdrop);
  }
  .canvas {
    position: relative;
    width: 1200px;
    height: 1116px;
  }
  .card {
    position: absolute;
    left: 240px;
    width: 720px;
    height: 450px;
    background: var(--card-white);
    box-shadow: 0 10px 24px var(--shadow);
    overflow: hidden;
  }
  .card--front { top: 88px; }
  .card--back { top: 578px; }
  .card-shapes {
    position: absolute;
    inset: 0;
    width: 720px;
    height: 450px;
  }
  .band { fill: var(--band-blue); }
  .panel { fill: var(--panel-navy); }
  .brand-name {
    position: absolute;
    left: 28px;
    top: 132px;
    width: 240px;
    font-family: "Arimo", Arial, sans-serif;
    font-weight: 700;
    font-size: 34px;
    letter-spacing: 0.5px;
    color: var(--brand-blue);
    line-height: 1.1;
    white-space: nowrap;
  }
  .contact {
    position: absolute;
    left: 330px;
    right: 14px;
    top: 258px;
    text-align: center;
    font-family: "Tinos", "Times New Roman", serif;
    font-style: normal;
    color: var(--text-light);
    font-size: 17px;
    line-height: 1.42;
  }
  .contact-street {
    font-weight: 700;
    font-size: 18px;
  }
  .person {
    position: absolute;
    left: 380px;
    right: 20px;
    top: 220px;
    text-align: center;
    color: var(--text-light);
  }
  .person-name {
    font-family: "Arimo", Arial, sans-serif;
    font-size: 34px;
    font-weight: 400;
    letter-spacing: 0.5px;
    line-height: 1.1;
  }
  .person-role {
    font-family: "Tinos", "Times New Roman", serif;
    font-size: 27px;
    line-height: 1.1;
  }
</style>
</head>
<body>
<main class="canvas">

  <section class="card card--front" aria-label="Business card, contact side">
    <svg class="card-shapes" viewBox="0 0 720 450" aria-hidden="true">
      <polygon class="band" points="317,0 720,0 720,450 241,450"/>
      <polygon class="panel" points="353,36 720,36 720,450 281,450"/>
    </svg>
    <div class="brand-name">HLM Services</div>
    <address class="contact">
      <div class="contact-street">14 ELM PARADE,</div>
      <div>MARSH ROAD, BEXLEY, KENT DA5 2QT</div>
      <div>Telephone: 020 7946 0321&nbsp; Fax: 020 7946 0847</div>
      <div>Mobile: 07700 900412</div>
      <div>danielhartley@hlmservicesltd.co.uk</div>
    </address>
  </section>

  <section class="card card--back" aria-label="Business card, name side">
    <svg class="card-shapes" viewBox="0 0 720 450" aria-hidden="true">
      <polygon class="band" points="317,0 720,0 720,450 241,450"/>
      <polygon class="panel" points="353,36 720,36 720,450 281,450"/>
    </svg>
    <div class="brand-name">HLM Services</div>
    <div class="person">
      <div class="person-name">DANIEL HARTLEY</div>
      <div class="person-role">Director</div>
    </div>
  </section>

</main>
</body>
</html>
```